Silver Kite Venture Series Travel Brochure

I'm looking for a brochure design for a new travel product - Silver Kite Venture Series, catering for students above 12 years old. Target audience are schools that do destination projects. Brochure to be read by head teacher, parents and students.

Brochure should be A4 in size, 4-6 pages. Format of brochure is hard cover (a folder) with inlet for flyers. Flyers for destinations will be updated from time to time.

Finished job needs to be converted to electronic format for website and email proposal usage.

Attached is text to be used on brochure. Order of section can be adjusted.

For "Elements of the trip", please understand the contents and explain/display it in a graphic form.

For flyer, please come out with a template that I can use for other destinations. The main elements - what's included, number of days, location for pictures, itinerary, educational focus, should be alterable. Attached are text for two sample destinations.
Also attached (tour itinerary example) a version of flyer that I like.

I'm attaching some pictures here. If you find more suitable pictures, please feel free to use them.

Reason: I'm extending the deadline of this project by 4 days, as I need to add details & photo of another travel specialist in personnel session (total of 3 members). Also, in view of the amount of work a designer has to do for this project, I'm giving you more time for submission. Please do not hesitate to be in touch should you need more than 4 days extension. Thank you.

Target Market(s)

Schools - especially the head teacher and parents, to send students above 12 years old to travel

Industry/Entity Type

Electronic

Requirements
Must have
• This is a travel brochure with education elements in it. Parents feel better when their children are travelling for a purpose and lead by responsible teachers/adults whom they can trust. So, the design has to emphasis that education elements and safety are our utmost priority.
Nice to have
• We specialise in environmental study. So, it is nice to have the environmental touch in the design.
Should not have
• Our target market segment is the Middle East, which can be quite sensitive to religion. I prefer not to have any religious related illustration on the design.

```html
<!DOCTYPE html>
<html lang="en">
<head>
<meta charset="utf-8">
<title>Silver Kite Venture Series – Brochure Spreads</title>
<link rel="stylesheet" href="https://fonts.googleapis.com/css2?family=Arvo:wght@400;700&family=PT+Serif:ital,wght@0,400;0,700;1,400&display=swap">
<style>
:root{
  --canvas:#eeeeee;
  --paper:#ffffff;
  --green:#39a535;
  --green-dark:#1f7f2b;
  --lime:#a5c93b;
  --blue:#4a90d0;
  --navy:#1d3f78;
  --ink:#2a2a2a;
  --photo-a:#6f8f9e;
  --photo-b:#3f5f3a;
}
*{box-sizing:border-box;margin:0;padding:0}
html,body{width:1200px;height:1028px;overflow:hidden;background:var(--canvas)}
body{position:relative;font-family:"PT Serif",Georgia,serif;color:var(--ink)}
.page{position:absolute;width:342px;height:466px;background:var(--paper);box-shadow:0 1px 4px rgba(0,0,0,.25);overflow:hidden}
.page-number{position:absolute;font-family:Arial,Helvetica,sans-serif;font-size:22px;color:#222}
.abs{position:absolute}
.heading{font-family:"Arvo",Georgia,serif;font-weight:700;color:var(--green);font-size:9.5px;line-height:1.2}
.body-text{font-size:5.7px;line-height:1.38;text-align:justify}
.body-text p{margin-bottom:3px}
.lead{font-variant:small-caps;font-weight:700;font-size:6.6px}
.strong{font-weight:700}
.italic{font-style:italic}
.white{color:#fff}
.cols-2{column-count:2;column-gap:8px}
.cols-3{column-count:3;column-gap:7px}
.label-block{font-family:"Arvo",Georgia,serif;font-weight:700;color:#fff;font-size:13px;line-height:1.05;text-transform:uppercase}
.photo{background:linear-gradient(160deg,var(--photo-a),var(--photo-b))}
.photo-person{background:linear-gradient(180deg,#b9b3ab,#6c6660)}
.sprout-area{position:absolute;background:linear-gradient(135deg,#cfe49a,#8cc63f)}
.rule{position:absolute;background:var(--green);width:4px}
.brand{position:absolute;display:flex;align-items:center;gap:4px}
.brand-mark{width:9px;height:9px;background:var(--navy)}
.brand-name{font-family:"PT Serif",Georgia,serif;font-size:6px;color:var(--navy);letter-spacing:.5px;text-transform:uppercase}
.faq-q{font-weight:700;font-size:5.6px;color:#fff}
.faq-a{font-style:italic;font-size:5.6px;padding-left:6px;margin-bottom:2px}
.faq-dark .faq-q{color:var(--navy)}
.diagram-label{position:absolute;font-size:4.8px;line-height:1.3;width:62px}
.diagram-label b{display:block;font-family:"Arvo",Georgia,serif;color:var(--green-dark);font-size:7px;margin-bottom:1px}
.contact{font-size:5px;line-height:1.45}
</style>
</head>
<body>

<section class="page page-intro" style="left:21px;top:25px">
  <div class="brand" style="left:14px;top:8px"><span class="brand-mark"></span><span class="brand-name">Marlow Crest Consulting</span></div>
  <div class="photo abs" style="left:16px;top:40px;width:172px;height:282px" role="img" aria-label="Photograph of an ancient stone wall winding over green hills"></div>
  <div class="abs" style="left:24px;top:92px;width:160px;font-family:'Arvo',Georgia,serif;font-weight:700;color:#fff;font-size:21px;line-height:1.05;text-transform:uppercase">Silver Kite Venture Series</div>
  <div class="sprout-area" style="left:190px;top:6px;width:70px;height:28px" role="img" aria-label="Green sprout illustration"></div>
  <div class="rule" style="left:192px;top:34px;height:296px"></div>
  <h2 class="heading abs" style="left:204px;top:76px;width:126px">What are Silver Kite Education – Silver Kite Venture Series tours?</h2>
  <div class="body-text abs" style="left:204px;top:122px;width:126px">
    <p><span class="lead">Our tours offer students and teachers</span> the opportunity to explore the world and learn through social interaction, physical challenges and real life involvements related to the curriculum. With a wide variety of experiences, students will be able to develop personal interests and self-belief and hold onto memories to last a lifetime. We want you to be curious about your surroundings, and we will help you to uncover the secrets of the world. You might have read or heard about Nepenthes, but do you know it is a carnivorous pitcher plant that looks like a monkey cup? We will show you several species in Malaysia, and take you on a fascinating journey to discover the wonders of the Malaysian rainforests.</p>
  </div>
  <div class="abs" style="left:16px;top:345px;width:310px;height:104px;background:var(--blue);padding:8px 9px">
    <div class="body-text white italic cols-3">
      <p><span class="lead">The tallest mountain in the world,</span> stands at nearly nine thousand metres above sea level. Do you know, although this mountain is claimed to be accurate, some suggest the height grows a few millimetres every year? Regardless, you will be amazed by the beauty of the mountain whilst hiking and experiencing the hospitality of the local people on your way.</p>
      <p><span class="lead">Many people are curious about the</span> great length of the ancient wall. Did you know that construction work went on for centuries and that a sticky rice soup was used to bind the bricks? We will take you there to examine its strength while you climb part of the wall and immerse yourself in ancient history.</p>
      <p>The upper part of the wall opened to visitors long ago. The feeling of the petals of a flower and wine espalied in all directions is an image that stays with you. <span class="lead">Finally, you</span> must walk in the steps of the ancient builders, visit some of the greatest museums and experience a rainforest and a countryside.</p>
    </div>
  </div>
</section>
<span class="page-number" style="left:368px;top:462px">1</span>

<section class="page page-education" style="left:420px;top:25px">
  <div class="photo abs" style="left:16px;top:56px;width:158px;height:392px;border-radius:0 80px 80px 0;background:linear-gradient(150deg,#8b9aa6,#3a4a3f 55%,#a87a3c)" role="img" aria-label="Photograph of a reflective steel sphere sculpture mirroring a city street"></div>
  <div class="sprout-area" style="left:140px;top:16px;width:62px;height:28px" role="img" aria-label="Green sprout illustration"></div>
  <div class="rule" style="left:176px;top:44px;height:410px"></div>
  <h2 class="heading abs" style="left:186px;top:64px">The role of education</h2>
  <div class="body-text abs" style="left:186px;top:82px;width:142px">
    <p><span class="lead">With teaching experience as part of our portfolios,</span> we understand the needs of teachers and the importance of relevant links to the curriculum. It is our aim, therefore, to tailor make tours for schools that fulfil key criteria but, at the same time, give students valuable opportunities to develop as individuals as well as team members. <span class="strong">Life time changes so often happen outside the classroom.</span></p>
    <p>With each tour, there will always be a strong focus on respect and empathy for others and appreciation of the experiences they have. By combining economic, social and environmental understanding in each country we visit, our goal is for each student to gain a clear perspective of the human condition and the human impact on the environment. <span class="strong">Beauty can be best appreciated by those who value it.</span></p>
    <p>Tours can be designed to support schools involved in the International Award; in particular, the Adventurous Journey aspect which focuses on adventure and discovery. All tours aim to develop an understanding of the environment and issues that face each country from a local as well as global perspective. Emphasis is also given to the importance of working together in a team with a common purpose.</p>
    <p>Each tour will have a main focus subject with other subjects integrated into the programme. Each tour will also have an environmental focus, which will be connected to a specific environmental project or issue in each country. As part of the preparation stage of the tour, students and teachers will be shown a presentation that will enhance greater understanding of environmental issues, both locally as well as in relation to the tour destination.</p>
  </div>
</section>
<span class="page-number" style="left:768px;top:462px">3</span>

<section class="page page-arrangements" style="left:811px;top:25px">
  <h2 class="heading abs" style="left:18px;top:40px">What else do we arrange?</h2>
  <div class="abs" style="left:16px;top:72px;width:124px;height:110px;background:var(--blue)"><div class="label-block abs" style="left:12px;top:48px">Pre Tour</div></div>
  <div class="abs" style="left:140px;top:58px;width:186px;height:124px;background:var(--lime);padding:6px 8px">
    <div class="body-text" style="font-size:5.8px;margin-bottom:4px"><span class="lead">We will prepare students and parents</span> for all aspects of the trip.</div>
    <div class="body-text cols-3" style="font-size:4.6px;text-align:left">
      <p><b>Passport:</b> at least six months validity is a must, we will check for you.</p>
      <p><b>Visas:</b> we will make sure you get the correct type of visa.</p>
      <p><b>Parental authorisation form:</b> students under the age of 18 must get the consent of their parents.</p>
      <p><b>Rooming:</b> we will organise twin or triple sharing rooms for students.</p>
      <p><b>Accommodation:</b> information will be given well before departure.</p>
      <p><b>Insurance:</b> we need personal insurance for each traveller.</p>
      <p><b>Meals:</b> we will inform of the types of meals on the trip.</p>
      <p><b>Packing list:</b> students will be coming back with full bags.</p>
      <p><b>Money:</b> we do not recommend carrying large sums of money.</p>
      <p><b>Special needs:</b> inform us of any dietary or medical needs in advance.</p>
    </div>
  </div>
  <div class="rule" style="left:136px;top:50px;height:132px"></div>
  <div class="sprout-area" style="left:246px;top:184px;width:66px;height:26px" role="img" aria-label="Green sprout illustration"></div>
  <div class="rule" style="left:246px;top:210px;height:46px"></div>
  <div class="body-text abs" style="left:20px;top:214px;width:222px;font-size:5.8px"><span class="lead">We will brief both students and parents</span> the detailed itinerary of each trip before departure. During the tour, students will be taught to be a responsible traveller, learn to look after themselves and their friends.</div>
  <div class="abs" style="left:16px;top:256px;width:206px;height:76px;background:var(--blue);padding:5px 7px">
    <div class="body-text cols-3 white" style="font-size:4.6px;text-align:left">
      <p><b>Clothing:</b> we will educate students to wear practical attire during different activities.</p>
      <p><b>Security:</b> we will ensure the students stick with their group at all times and remain close to a tour director.</p>
      <p><b>Staying in touch:</b> tour directors and hotel contacts are shared with parents.</p>
      <p><b>Punctuality:</b> activities are pre-scheduled for each day, so students should respect the timings.</p>
      <p>Plenty of free time will be given for students to relax and reflect on their day.</p>
    </div>
  </div>
  <div class="abs" style="left:222px;top:256px;width:104px;height:76px;background:var(--green)"><div class="label-block abs" style="left:10px;top:26px;text-align:center;width:84px">During the Tour</div></div>
  <div class="sprout-area" style="left:58px;top:336px;width:64px;height:26px" role="img" aria-label="Green sprout illustration"></div>
  <div class="rule" style="left:136px;top:346px;height:102px"></div>
  <div class="abs" style="left:16px;top:374px;width:120px;height:74px;background:var(--green)"><div class="label-block abs" style="left:12px;top:30px">Post Tour</div></div>
  <div class="body-text abs" style="left:146px;top:366px;width:176px;font-size:5.8px"><span class="lead">Our tour directors will guide</span> participating students to log their trips.</div>
  <div class="abs" style="left:140px;top:390px;width:186px;height:58px;background:var(--lime);padding:6px 8px">
    <div class="body-text cols-2" style="font-size:4.8px;text-align:left">
      <p><b>Travel journal:</b> this could be in the form of writing or photographs.</p>
      <p><b>Assignment:</b> depends on destination, the tour director will assign some fun tasks to the group. We will compile and conclude after the tour.</p>
    </div>
  </div>
</section>
<span class="page-number" style="left:1160px;top:462px">5</span>

<section class="page page-team" style="left:21px;top:528px">
  <div class="sprout-area" style="left:12px;top:12px;width:66px;height:28px" role="img" aria-label="Green sprout illustration"></div>
  <div class="rule" style="left:30px;top:40px;height:156px"></div>
  <h2 class="heading abs" style="left:42px;top:72px;font-size:11px">Who are we?</h2>
  <div class="body-text abs" style="left:42px;top:90px;width:286px;font-size:6px">
    <p><span class="lead">We are specialist travel management consultants,</span> offering a diversified range of travel services to our customers. With our vast knowledge of destinations, years of teaching experience and our passion to open up the world to students and teachers, we are able to tailor make trips based on your needs and requirements and make sure they are exactly right for the level and needs of your students.</p>
    <p>We ensure peace of mind, with detailed pre-tour preparation, clear guidelines and expectations during the tours and post tour reports and assessments. We carry out a thorough risk management process before finalising your itinerary, taking into account the latest political situation, the likely weather, economic conditions and other elements. Safety is our utmost priority.</p>
  </div>
  <div class="photo-person abs" style="left:16px;top:200px;width:60px;height:84px" role="img" aria-label="Portrait photograph of travel specialist Lena Avery"></div>
  <div class="abs" style="left:76px;top:196px;width:266px;height:96px;background:var(--lime);padding:6px 8px">
    <div class="body-text cols-2 italic" style="font-size:4.9px"><p><span class="heading white" style="font-size:8px;font-style:normal">Lena Avery</span> <span class="lead white">has a passion for travel.</span> She was born and brought up in a coastal city and moved to the Gulf in 2001. With her travel management background, she set up her travel business after years of working with tour operators. She has travelled extensively in Europe and Africa, and helped many groups arrange educational tours.</p><p>She has been on many expeditions and loves to discover hidden gems. She always checks out the specialties of each destination before putting them together as a tour package. Her expertise includes planning, guiding, sporting related travel and catering for various groups.</p></div>
  </div>
  <div class="photo-person abs" style="left:16px;top:296px;width:60px;height:84px" role="img" aria-label="Portrait photograph of travel specialist Owen Hartley"></div>
  <div class="abs" style="left:76px;top:292px;width:266px;height:94px;background:var(--blue);padding:6px 8px">
    <div class="body-text cols-2 italic white" style="font-size:4.9px"><p><span class="heading" style="font-size:8px;font-style:normal;color:#fff">Owen Hartley</span> <span class="lead">is a freelance environmental education trainer,</span> with many years teaching experience, especially within environmental science and outdoor education. He has lived and worked in several countries and coordinated environmental education and outreach programmes.</p><p>In recent years he has led environmental advocacy and sustainability events in the region. Currently he runs school and corporate environmental workshops and writes environmental education programmes to further enhance environmental awareness among students.</p></div>
  </div>
  <div class="photo-person abs" style="left:16px;top:390px;width:60px;height:70px" role="img" aria-label="Portrait photograph of travel specialist Rafe"></div>
  <div class="abs" style="left:76px;top:386px;width:266px;height:80px;background:var(--green);padding:6px 8px">
    <div class="body-text cols-2 italic white" style="font-size:4.9px"><p><span class="heading" style="font-size:8px;font-style:normal;color:#fff">Rafe</span> <span class="lead">is a professional mountaineer</span> and expedition leader. He has been trekking, rock climbing and mountaineering since moving to the region. He has climbed and trekked in many ranges and guided groups of students on their first summits.</p><p>In a previous life he worked in finance, then studied teaching and training. He has managed trips across Asia and Europe and has seen more peaks than he can count.</p></div>
  </div>
</section>
<span class="page-number" style="left:368px;top:990px">2</span>

<section class="page page-elements" style="left:420px;top:528px">
  <h2 class="heading abs" style="left:18px;top:40px">What are the elements of the trips?</h2>
  <svg class="abs" style="left:0;top:0" width="342" height="466" viewBox="0 0 342 466" aria-hidden="true">
    <g stroke="var(--green)" stroke-width=".7" stroke-dasharray="1.5 1.5" fill="none">
      <line x1="171" y1="232" x2="171" y2="98"/>
      <line x1="171" y1="232" x2="268" y2="128"/>
      <line x1="171" y1="232" x2="292" y2="205"/>
      <line x1="171" y1="232" x2="270" y2="320"/>
      <line x1="171" y1="232" x2="190" y2="358"/>
      <line x1="171" y1="232" x2="92" y2="358"/>
      <line x1="171" y1="232" x2="40" y2="312"/>
      <line x1="171" y1="232" x2="36" y2="220"/>
      <line x1="171" y1="232" x2="70" y2="126"/>
    </g>
    <g fill="var(--green)">
      <circle cx="171" cy="98" r="2.5"/><circle cx="268" cy="128" r="2.5"/><circle cx="292" cy="205" r="2.5"/>
      <circle cx="270" cy="320" r="2.5"/><circle cx="190" cy="358" r="2.5"/><circle cx="92" cy="358" r="2.5"/>
      <circle cx="40" cy="312" r="2.5"/><circle cx="36" cy="220" r="2.5"/><circle cx="70" cy="126" r="2.5"/>
    </g>
    <circle cx="171" cy="232" r="98" fill="#8cc63f"/>
    <circle cx="171" cy="232" r="90" fill="var(--green)"/>
    <circle cx="171" cy="232" r="50" fill="#d7ecbd"/>
    <circle cx="171" cy="232" r="45" fill="var(--green-dark)"/>
    <g fill="#fff">
      <circle cx="171" cy="162" r="11"/><circle cx="222" cy="180" r="11"/><circle cx="240" cy="232" r="11"/>
      <circle cx="222" cy="284" r="11"/><circle cx="180" cy="302" r="11"/><circle cx="140" cy="298" r="11"/>
      <circle cx="112" cy="272" r="11"/><circle cx="102" cy="226" r="11"/><circle cx="120" cy="182" r="11"/>
    </g>
    <g font-family="Arvo, Georgia, serif" font-weight="700" font-size="10" fill="#fff" text-anchor="middle">
      <text x="171" y="224">WHAT'S</text>
      <text x="171" y="236">INCLUDED</text>
      <text x="171" y="248">IN THE</text>
      <text x="171" y="260">COST?</text>
    </g>
  </svg>
  <div class="diagram-label" style="left:160px;top:62px"><b>Tours</b>We will design an itinerary for the students to explore the essence of each destination with a strong educational element.</div>
  <div class="diagram-label" style="left:262px;top:82px"><b>Full time tour director</b>This person is your guide, friend and support throughout the tour.</div>
  <div class="diagram-label" style="left:284px;top:168px;width:50px"><b>Visa</b>We will assist with entry visas for all of the participants.</div>
  <div class="diagram-label" style="left:262px;top:324px;width:66px"><b>Local tour guide</b>We will have licensed local guides with extensive knowledge of each destination.</div>
  <div class="diagram-label" style="left:182px;top:362px;width:70px"><b>Local collaboration</b>We arrange collaboration with local community, based on your requirements.</div>
  <div class="diagram-label" style="left:60px;top:362px;width:66px"><b>Food &amp; drinks</b>We will include all meals throughout the journey, ensuring quality and suitability.</div>
  <div class="diagram-label" style="left:14px;top:272px;width:54px"><b>Travel insurance</b>Travel insurance for each of the students is compulsory.</div>
  <div class="diagram-label" style="left:12px;top:178px;width:44px"><b>Air ticket</b>We will arrange the best flight options available to you.</div>
  <div class="diagram-label" style="left:40px;top:80px;width:72px"><b>Accommodation</b>We organise suitable lodging for students at strategic locations with twin or triple rooms.</div>
  <div class="body-text abs" style="left:18px;top:420px;width:250px;font-size:6px"><span class="lead">Any situations that arise on the trips,</span> be it minor or major issues, will be handled professionally and promptly by our tour directors.</div>
</section>
<span class="page-number" style="left:768px;top:990px">4</span>

<section class="page page-faq" style="left:811px;top:528px">
  <h2 class="heading abs" style="left:18px;top:38px">FAQ</h2>
  <div class="abs" style="left:16px;top:62px;width:124px;height:176px;background:var(--navy)"><div class="label-block abs" style="left:14px;top:80px">Parents</div></div>
  <div class="sprout-area" style="left:194px;top:36px;width:64px;height:26px" role="img" aria-label="Green sprout illustration"></div>
  <div class="abs" style="left:140px;top:62px;width:186px;height:176px;background:var(--lime);padding:8px 8px">
    <p class="faq-q">How do I know I am getting value for money?</p><p class="faq-a">All aspects of the cost for the tours are carefully planned, with comprehensive subject focused.</p>
    <p class="faq-q">If my child gets sick or injured on the trip, what arrangements will be made?</p><p class="faq-a">We have comprehensive knowledge of all local services and foreign/overseas supports.</p>
    <p class="faq-q">Can I join my children, whether for the whole duration or just part of it?</p><p class="faq-a">Yes, we can normally make these types of arrangement, but only the tours during holiday periods and it is subject to individual school's choice.</p>
    <p class="faq-q">Can my child extend his/her trip?</p><p class="faq-a">Yes, this would only happen during holiday periods and subject to individual school.</p>
    <p class="faq-q">Are vaccinations needed?</p><p class="faq-a">Depends on destination, this will be advised with sufficient time before departure.</p>
  </div>
  <div class="abs faq-dark" style="left:18px;top:256px;width:212px">
    <p class="faq-q">Are the guides during the trip fully qualified and first-aid trained?</p><p class="faq-a">Yes.</p>
    <p class="faq-q">How much travel time will there be?</p><p class="faq-a">Travel times vary but are kept to the minimum possible to maximise activity time.</p>
    <p class="faq-q">How up to date are your programmes?</p><p class="faq-a">Programmes are checked and revised frequently.</p>
    <p class="faq-q">How safe are the places we stay?</p><p class="faq-a">Safety is our top priority and accommodation is chosen very carefully.</p>
    <p class="faq-q">How do I arrange with you a pre-visit to the school?</p><p class="faq-a">If you are interested in our tour, we can arrange a meeting at your school. We will gather your requirements and needs during the meeting and then come out with a suitable programme and costing.</p>
    <p class="faq-q">What is the smallest/largest number of students I can bring?</p><p class="faq-a">Ideally, smallest number is 8 students and largest number is not more than 40 students. Our ratio of students to tour director is 8:1.</p>
  </div>
  <div class="sprout-area" style="left:246px;top:228px;width:60px;height:24px" role="img" aria-label="Green sprout illustration"></div>
  <div class="abs" style="left:234px;top:252px;width:92px;height:170px;background:var(--navy)"><div class="label-block abs" style="left:10px;top:130px">Teachers</div></div>
  <div class="contact abs" style="left:18px;top:424px">
    <b>Marlow Crest Travel</b><br>Unit 4, Harbour Point, Meridian Bay<br><b>Tel:</b> +00 1 555 0142<br><b>Fax:</b> +00 1 555 0143<br><b>Email:</b> hello@marlowcrest.example
  </div>
</section>
<span class="page-number" style="left:1160px;top:990px">6</span>

</body>
</html>
```